Dietitian needs awesome business card

I need a contemporary design that's eye catching but professional.
My card is to given to doctors, specialists and patients alike.
I manage patients with chronic diseases
I have uploaded my logo and current business card, I would also like the other Certified Clinical Nutritionist logo incorporated into the design

Target Market(s)

Doctors, specialists and patients

Industry/Entity Type

Healthcare

Contact Information for Business Card

www.brightfieldnutrition.com.au
Ph: 0427 561 903
Fax: 6457 2183
email: marcus.k.diet@fernmail.com
Space on the back of the card with: Appointment date, Appointment time and appointment location

Font styles to use
Serif

Colors
fbee3e
876aae
ffc214

Requirements
Must have
• My Logo
• Certified Clinical Nutritionist Logo
• My 4 locations - Pinebrook Medical Centre, North Corrin Health, Hollis Medical, Ashcombe Doctors Surgery
Nice to have
• I like the colours in my current business card

```html
<!DOCTYPE html>
<html lang="en">
<head>
<meta charset="utf-8">
<title>Brightfield Nutrition &amp; Dietetics – Business Card</title>
<link rel="stylesheet" href="https://fonts.googleapis.com/css2?family=Philosopher&family=PT+Sans&family=Noto+Serif&display=swap">
<style>
  :root {
    --page-bg: #e6e6e6;
    --card-bg: #ffffff;
    --navy: #1f3293;
    --blue: #1e6fc4;
    --green: #8dc63f;
    --leaf: #7cb82f;
    --text-grey: #4a4a4a;
    --rule-grey: #b9b9b9;
    --badge-orange: #f47a20;
    --forest: #4a5a3c;
    --white: #ffffff;
  }
  * { box-sizing: border-box; margin: 0; padding: 0; }
  html, body {
    width: 1105px; height: 1200px; overflow: hidden;
    background: var(--page-bg);
  }
  .card {
    position: absolute;
    left: 180px;
    width: 746px; height: 425px;
    background: var(--card-bg);
    overflow: hidden;
  }
  .card--front { top: 120px; }
  .card--back { top: 650px; }

  /* Front */
  .brand {
    position: absolute; left: 56px; top: 150px;
    display: flex; align-items: center; gap: 12px;
  }
  .brand__dot {
    flex: none;
    width: 56px; height: 56px; border-radius: 50%;
    background: var(--navy);
  }
  .brand__name {
    font-family: "Philosopher", sans-serif;
    font-size: 23px; line-height: 1.15;
    color: var(--navy);
    white-space: nowrap;
  }
  .divider {
    position: absolute; left: 362px; top: 95px;
    width: 1px; height: 180px; background: var(--rule-grey);
  }
  .person { position: absolute; left: 390px; top: 100px; }
  .person__name {
    font-family: "Philosopher", sans-serif;
    font-weight: 400;
    font-size: 28px; color: var(--navy);
  }
  .person__title {
    font-family: "PT Sans", sans-serif;
    font-size: 20px; color: var(--leaf); margin-top: 2px;
  }
  .contacts { list-style: none; margin-top: 14px; }
  .contacts li {
    display: flex; align-items: center; gap: 10px;
    font-family: "PT Sans", sans-serif;
    font-size: 19px; color: var(--text-grey);
    height: 29px;
  }
  .contacts svg { flex: none; width: 17px; height: 17px; fill: var(--navy); }
  .web-band {
    position: absolute; left: 0; top: 366px;
    width: 100%; height: 39px;
    background: linear-gradient(90deg, var(--navy) 0%, var(--blue) 70%, var(--navy) 74%, var(--blue) 82%, var(--green) 100%);
  }
  .web-band__url {
    position: absolute; left: 131px; top: 7px;
    font-family: "Noto Serif", serif;
    font-size: 18px; letter-spacing: 1px; color: var(--white);
  }
  .web-band__dot {
    position: absolute; left: 598px; top: -8px;
    width: 52px; height: 52px; border-radius: 50%;
    background: var(--white); border: 5px solid var(--leaf);
  }

  /* Back */
  .credential-badge {
    position: absolute; left: 119px; top: 62px;
    width: 178px; height: 84px; border-radius: 3px;
    background: var(--badge-orange);
  }
  .appointment {
    position: absolute; left: 345px; top: 58px;
    font-family: "PT Sans", sans-serif; color: var(--navy);
  }
  .appointment__row { font-size: 21px; height: 38px; white-space: nowrap; }
  .appointment__fill { letter-spacing: 1px; font-size: 16px; }
  .appointment__ampm { font-size: 15px; }
  .notes { position: absolute; left: 41px; top: 196px; width: 645px; }
  .notes__line { height: 43px; border-top: 1px solid var(--rule-grey); }
  .locations {
    position: absolute; left: 41px; top: 318px; width: 645px;
    text-align: center;
    font-family: "PT Sans", sans-serif;
    font-size: 15px; color: var(--navy);
    white-space: nowrap;
  }
  .region-strip {
    position: absolute; left: 0; top: 363px;
    width: 100%; height: 62px;
    background: linear-gradient(90deg, #3f4f34, var(--forest) 50%, #3f4f34);
  }
  .region-strip__text {
    position: absolute; left: 0; right: 0; top: 14px;
    text-align: center;
    font-family: "Noto Serif", serif;
    font-size: 25px; color: var(--white);
  }
</style>
</head>
<body>
  <section class="card card--front">
    <div class="brand">
      <span class="brand__dot"></span>
      <div class="brand__name">Brightfield<br>Nutrition &amp; Dietetics</div>
    </div>
    <div class="divider"></div>
    <div class="person">
      <h1 class="person__name">Marcus Kellner</h1>
      <p class="person__title">Nutritionist &amp; Chef</p>
      <ul class="contacts">
        <li><svg viewBox="0 0 24 24" aria-hidden="true"><path d="M6.6 10.8a15 15 0 0 0 6.6 6.6l2.2-2.2c.3-.3.7-.4 1-.2 1.1.4 2.3.6 3.6.6.6 0 1 .4 1 1V20c0 .6-.4 1-1 1A17 17 0 0 1 3 4c0-.6.4-1 1-1h3.5c.6 0 1 .4 1 1 0 1.3.2 2.5.6 3.6.1.3 0 .7-.2 1z"/></svg>0427 561 903</li>
        <li><svg viewBox="0 0 24 24" aria-hidden="true"><path d="M6 2h9l3 3v5H6zM3 11h18v8h-3v3H6v-3H3zm5 5v4h8v-4z"/></svg>6457 2183</li>
        <li><svg viewBox="0 0 24 24" aria-hidden="true"><path d="M2 5h20v14H2zm2 2v.5l8 5 8-5V7l-8 5z"/></svg>marcus.k.diet@fernmail.com</li>
      </ul>
    </div>
    <div class="web-band">
      <span class="web-band__url">www.brightfieldnutrition.com.au</span>
      <span class="web-band__dot"></span>
    </div>
  </section>

  <section class="card card--back">
    <div class="credential-badge" role="img" aria-label="Certified Clinical Nutritionist badge"></div>
    <div class="appointment">
      <p class="appointment__row">Date : <span class="appointment__fill">...................................</span></p>
      <p class="appointment__row">Time : <span class="appointment__fill">.............................</span> <span class="appointment__ampm">AM/PM</span></p>
      <p class="appointment__row">Location : <span class="appointment__fill">............................</span></p>
    </div>
    <div class="notes">
      <div class="notes__line"></div>
      <div class="notes__line"></div>
      <div class="notes__line"></div>
    </div>
    <p class="locations">Pinebrook Medical Centre · North Corrin Health · Hollis Medical · Ashcombe Doctors Surgery</p>
    <div class="region-strip" role="img" aria-label="Dark green wood grain texture band">
      <p class="region-strip__text">Dietitian for Launceston &amp; North East Tasmania</p>
    </div>
  </section>
</body>
</html>
```